Cruise Booking Website

Cruise search and booking website

This project is a redesign of a cruise booking website we did a few years ago.

The current website is located here: http://voyage.pylonworks.example/en/

It's not fully functional but gives you ad idea how miserable the old design was.

All the information about cruises, cruise lines, destinations, ports and shore excursions will be similar to http://www.sailquest.example/
Actual search pages (form, results, single result, sailing and cabin selection, ship info, booking) will have EXACTLY the same info as sailquest.example

We like the style of http://harborfleetdesk.example, it's quite modern, good spacing, not overloaded with information. So you can use it as an example of what we like, not what we want as a final result for us. Please, don't copy it. The result should not be possible to resemble the harborfleetdesk.example, because our site has to be unique. This is important!
If you submit a design that clearly reminds another cruise site it will be rejected!

Also the mockup provided is just to give you the basic structure and show what information has to be present on the page. It doesn't mean the layout has to be the same as a mockup. The layout is up to the designer.

I've updated the mockup to be more generic so it doesn't confuse you:
https://files.boxvault.example/s/k7m2qp9wz4hx/Home%20page.png

When you're adding social sharing icons like plazanet/chirpline you have to use chinese ones instead:
https://files.boxvault.example/s/t3nr8vx5lc2e/chinese-social-icons.png
Originals: http://minilk.example/qR7t

We'll start with home page first and after it's approved inner pages can be designed.

I know the cost of the project doesn't look high, but the task is straight forward and doesn't require to be very original, it's better to follow existing design and layout patterns that proved to work well.
That's why I encourage you to choose a template to build the design on top of one of https://themeparlor.example/ themes if it will save the design work, will be easier and faster for you. So it will be more like a customization than a new design from scratch.

Mockups, site map and logo files:
- https://files.boxvault.example/sh/h48dm2rs73fkpw/QvnbW2Xz8e

Website tree:
- https://sheets.papernest.example/document/d/7xPqR2mLw9sTk4VbN8cHj3YzA6eUf5GdKo1iMnBv/edit?usp=sharing
Updates

So far a lot of designs are just copying http://www.harborfleetdesk.example/ - we don't like it!

We like the style of harborfleetdesk.example, it's quite modern, good spacing, not overloaded with information. So you can use it as an example of what we like, not what we want as a final result for us. Please, don't copy it. The result should not be possible to resemble the harborfleetdesk.example, because our site has to be unique. This is important!

Target Market(s)

Chinese travellers

Industry/Entity Type

Build

Requirements
Must have
• * White, blue and red
* Large spacing, not too much information cramped into a small space like sailquest.example or the current website
* More "hidden" info in popups, tabs and so on, so not to many things are visible at the same time
* Compatible with kestrel scaffold styling (for easier coding):
- http://kestrelkit.codeshelf.example/scaffold/index.html
- http://skinmarket.example/
* Feel free to propose to build the design on top of one of https://themeparlor.example/ themes if it will save the design work, will be easier and faster for you

```html
<!DOCTYPE html>
<html lang="en">
<head>
<meta charset="utf-8">
<title>Bluewake Cruises – Home</title>
<link href="https://fonts.googleapis.com/css2?family=Open+Sans:wght@300;400;600;700&display=swap" rel="stylesheet">
<style>
:root{
  --blue-deep:#1f5f93;
  --blue-mid:#2b78b6;
  --blue-head:#1d6bad;
  --blue-sky:#4aa8ef;
  --red:#d8413a;
  --red-dark:#c5362f;
  --grey-bg:#ececec;
  --grey-line:#d6d6d6;
  --text:#333;
  --muted:#888;
  --white:#fff;
}
*{box-sizing:border-box;margin:0;padding:0}
html,body{width:798px;height:1200px;overflow:hidden}
body{font-family:"Open Sans",Arial,sans-serif;color:var(--text);background:var(--white);position:relative;font-size:9px}
.abs{position:absolute}
a{color:inherit;text-decoration:none}

/* header + hero */
.hero-bg{left:0;top:0;width:798px;height:342px;background:linear-gradient(180deg,#2e6b9c 0%,#2a6d9f 30%,#24699d 55%,#2f7cb2 100%)}
.hero-bg::after{content:"";position:absolute;left:0;right:0;bottom:0;height:2px;background:var(--red)}
.brand{left:32px;top:14px;display:flex;align-items:center;gap:8px;color:var(--white);font-weight:700;font-size:21px;letter-spacing:.2px}
.brand .dot{width:26px;height:26px;border-radius:50%;background:var(--white)}
.brand small{display:block;font-size:8px;font-weight:400;opacity:.85;letter-spacing:.5px}
.search{left:503px;top:14px;width:116px;height:15px;border-radius:8px;background:var(--white)}
.search-label{left:626px;top:13px;color:var(--white);font-size:11px}
.adv{left:503px;top:35px;color:#cfe3f5;font-size:8.5px;text-decoration:underline}
.toplinks{left:688px;top:6px;width:80px;color:var(--white);font-size:9px;list-style:none}
.toplinks li{border-bottom:1px solid rgba(255,255,255,.6);padding:1px 0 2px}
.toplinks li:last-child{border:0}
.nav{left:30px;top:60px;width:738px;height:28px;background:#e6e6e6;display:flex;align-items:center;justify-content:space-around;padding:0 14px;font-size:9.6px;color:#333;list-style:none}
.nav li::after{content:" ⌄";color:var(--red);font-size:9px}
.hero-title{left:119px;top:133px;color:var(--white);font-weight:300;font-size:25px;letter-spacing:.5px}
.hero-title b{font-weight:700}
.hero-box{left:118px;top:181px;width:303px;height:70px;background:rgba(41,139,214,.85);color:var(--white);font-size:9px;line-height:16px;padding:4px 8px}
.hero-photo{left:484px;top:122px;width:176px;height:174px;border:3px solid var(--white);border-radius:3px;background:linear-gradient(160deg,#c9dff0 0%,#e7c9a4 45%,#9c7a58 100%)}
.badge{left:467px;top:249px;width:60px;height:60px;border-radius:50%;background:var(--white);border:3px solid var(--red);color:var(--red);font-size:11px;font-weight:700;text-align:center;line-height:12px;padding-top:17px;transform:rotate(15deg)}
.arrow{top:170px;width:24px;height:58px;background:rgba(30,80,120,.6);display:flex;align-items:center;justify-content:center}

/* strip */
.strip{left:0;top:344px;width:798px;height:86px;background:#f4f4f4}
.hotline{left:30px;top:352px;width:170px;height:37px;border:1px solid var(--blue-mid);background:var(--white);display:flex;align-items:center;padding-left:10px;gap:6px;font-size:10px}
.hotline b{font-weight:400;font-size:13px;color:var(--blue-deep)}
.acct{top:364px;font-size:9.6px;display:flex;align-items:center;gap:4px}

/* feature cards */
.card{top:403px;width:171px;height:140px;background:var(--grey-bg)}
.card .img{height:93px}
.card h3{font-weight:400;font-size:10.5px;margin:12px 0 0 9px}
.more{display:inline-flex;align-items:center;gap:6px;margin:3px 0 0 9px;background:var(--white);font-size:8px;color:var(--red);padding-right:6px}
.more i{width:11px;height:11px;background:var(--red);color:var(--white);font-style:normal;font-size:10px;line-height:11px;text-align:center}
.finder{left:598px;top:403px;width:172px;height:140px;border:1px solid var(--grey-line);background:var(--white)}
.finder h4{background:var(--red);color:var(--white);text-align:center;font-size:11px;letter-spacing:.8px;height:19px;line-height:19px;font-weight:600}
.sel{position:absolute;height:13px;border:1px solid #aaa;font-size:7.5px;padding-left:3px;line-height:11px;background:var(--white)}
.sel::after{content:"⇕";position:absolute;right:0;top:0;width:11px;border-left:1px solid #aaa;text-align:center;height:11px}
.finder .lbl{position:absolute;font-size:6.5px}
.finder .go{position:absolute;left:21px;top:120px;width:129px;height:14px;background:var(--blue-head);color:var(--white);font-size:9px;text-align:center;line-height:14px;font-weight:600;letter-spacing:.5px}

/* info columns */
.ring{top:573px;width:76px;height:76px;border-radius:50%;border:1px solid var(--red);display:flex;align-items:center;justify-content:center;color:var(--red)}
.info{top:660px;width:200px}
.info h3{font-weight:400;font-size:12px}
.info p{color:var(--muted);font-size:8.3px;line-height:11.5px;margin-top:2px}
.info p a{color:var(--red)}
.rule{left:30px;top:755px;width:738px;height:1px;background:#e09a96}
.deals-title{left:29px;top:758px;font-weight:300;font-size:23px;color:#555}

/* deals */
.deal{top:793px;width:182px;height:188px;background:var(--grey-bg);text-align:center}
.deal .head{color:var(--white);font-weight:300;font-size:15px;display:flex;align-items:center;justify-content:center}
.deal .body{position:absolute;left:4px;right:4px;background:var(--white)}
.deal p{font-size:8.3px;line-height:11.5px;color:#666;padding:0 12px}
.deal p a{color:var(--red)}
.plan{display:inline-block;background:var(--red);color:var(--white);font-size:7.5px;font-weight:700;letter-spacing:.4px;width:80px;height:16px;line-height:16px}
.mini{display:flex;gap:10px;align-items:center;text-align:left;font-size:7.6px;line-height:9.5px;padding:6px 10px 0}
.mini .thumb{width:38px;height:38px;flex:none}

/* partners + footer */
.partners{left:0;top:1008px;width:798px;height:55px;background:var(--red);color:var(--white)}
.partners h2{position:absolute;left:34px;top:13px;font-weight:300;font-size:20px}
.plist{position:absolute;left:288px;top:20px;display:flex;gap:28px;font-size:11px;font-weight:600;letter-spacing:.3px}
.footer{left:0;top:1063px;width:798px;height:137px;background:var(--blue-sky);color:#10243a}
.flist{position:absolute;top:22px;list-style:none;font-size:8px;line-height:14px}
.flist li::before{content:"";display:inline-block;width:3px;height:3px;background:#10243a;margin-right:7px;vertical-align:middle}
.social{position:absolute;width:18px;height:18px;border-radius:4px}
.frule{position:absolute;left:30px;top:100px;width:738px;height:1px;background:#2c6aa8}
.copy{position:absolute;top:107px;width:100%;text-align:center;font-size:8px;line-height:13px}
</style>
</head>
<body>

<div class="abs hero-bg"></div>
<div class="abs brand"><span class="dot"></span><span>Bluewake Cruises<small>bluewake.example</small></span></div>
<div class="abs search"></div>
<div class="abs search-label">Search</div>
<a class="abs adv">Advance Search</a>
<ul class="abs toplinks"><li>BOOKING</li><li>ONLINE BOOKING</li><li>MEMBERS CENTRE</li></ul>
<ul class="abs nav">
  <li>DESTINATIONS</li><li>CRUISE LINES</li><li>SHORE ACTIVITIES</li><li>PROMOTIONS</li><li>CRUISE NEWS</li><li>BLOG</li><li>FAQ(Q&amp;A)</li><li>CONTACT US</li>
</ul>
<h1 class="abs hero-title">WELCOME TO <b>Bluewake</b></h1>
<p class="abs hero-box">Cruises are offered throughout the world and for each destination there are a number of cruise lines to choose from. From contemporary cruise lines to luxury cruise lines each cruise line offers different itineraries, features and options.</p>
<div class="abs hero-photo" role="img" aria-label="Couple on a cruise ship deck at sunset"></div>
<div class="abs badge">BEST<br>VALUE</div>
<div class="abs arrow" style="left:30px"><svg width="10" height="14"><path d="M8 1 2 7l6 6" stroke="#fff" stroke-width="2" fill="none"/></svg></div>
<div class="abs arrow" style="left:746px"><svg width="10" height="14"><path d="M2 1l6 6-6 6" stroke="#fff" stroke-width="2" fill="none"/></svg></div>

<div class="abs strip"></div>
<div class="abs hotline">
  <svg width="16" height="22" viewBox="0 0 16 22"><path d="M4 1c-3 2-4 6-2 11s5 8 9 9l3-3-3-4-3 1c-1-1-3-5-3-7l2-2-2-5z" fill="var(--red)"/></svg>
  Hotline: <b>4008 512 390</b>
</div>
<div class="abs acct" style="left:604px"><svg width="16" height="16"><rect x="1" y="3" width="11" height="11" fill="none" stroke="var(--red)" stroke-width="1.6"/><path d="M7 9l7-7" stroke="var(--red)" stroke-width="2"/></svg>REGISTER</div>
<div class="abs acct" style="left:690px"><svg width="16" height="16"><rect x="4" y="1" width="10" height="13" fill="none" stroke="var(--red)" stroke-width="1.6"/><path d="M1 8h8M6 5l3 3-3 3" stroke="var(--red)" stroke-width="1.6" fill="none"/></svg>MY ACCOUNT</div>

<div class="abs card" style="left:30px"><div class="img" role="img" aria-label="Cruise ship at sea" style="background:linear-gradient(180deg,#6fa6d6,#2f6fae)"></div><h3>Cruise lines</h3><a class="more"><i>+</i>Read More</a></div>
<div class="abs card" style="left:219px"><div class="img" role="img" aria-label="Rocky coastline with blue sea" style="background:linear-gradient(180deg,#8fc3ea,#2d7aa8 60%,#7d7e6a)"></div><h3>Shore Activites</h3><a class="more"><i>+</i>Read More</a></div>
<div class="abs card" style="left:409px"><div class="img" role="img" aria-label="Ship theatre interior" style="background:linear-gradient(180deg,#c8953f,#6a4a2b)"></div><h3>Cruise news</h3><a class="more"><i>+</i>Read More</a></div>

<div class="abs finder">
  <h4>FIND YOUR CRUISE</h4>
  <div class="sel" style="left:21px;top:26px;width:130px">Popular Destinations</div>
  <div class="sel" style="left:21px;top:48px;width:61px">Any Length</div>
  <div class="sel" style="left:89px;top:48px;width:62px">Any Month</div>
  <div class="sel" style="left:21px;top:70px;width:130px">Any Cruise Lines</div>
  <span class="lbl" style="left:21px;top:89px">AGE 25+</span>
  <span class="lbl" style="left:89px;top:89px">AGE 0-24</span>
  <div class="sel" style="left:21px;top:100px;width:61px">2</div>
  <div class="sel" style="left:89px;top:100px;width:62px">0</div>
  <div class="go">SEARCH CRUISE</div>
</div>

<div class="abs ring" style="left:108px"><span style="font-weight:700;font-size:16px">BLOG</span></div>
<div class="abs ring" style="left:361px"><span style="font-weight:700;font-size:40px">?</span></div>
<div class="abs ring" style="left:614px"><svg width="42" height="28" viewBox="0 0 42 28"><path d="M4 14l30-10 4 8-6 10H10z" fill="var(--red)"/><path d="M12 18h22" stroke="#fff" stroke-width="1.5"/></svg></div>

<div class="abs info" style="left:41px"><h3>Blog</h3><p>Lorem Ipsum is simply dummy text of the printing and typesetting industry. Lorem Ipsum has been the industry's standard dummy text ever since the 1500s, <a>Learn More &gt;</a></p></div>
<div class="abs info" style="left:294px"><h3>FAQ(Q&amp;A)</h3><p>Lorem Ipsum is simply dummy text of the printing and typesetting industry. Lorem Ipsum has been the industry's standard dummy text ever since the 1500s, <a>Learn More &gt;</a></p></div>
<div class="abs info" style="left:547px"><h3>Ports</h3><p>Lorem Ipsum is simply dummy text of the printing and typesetting industry. Lorem Ipsum has been the industry's standard dummy text ever since the 1500s, <a>Learn More &gt;</a></p></div>

<div class="abs rule"></div>
<h2 class="abs deals-title">Our Deals</h2>

<div class="abs deal" style="left:30px">
  <div class="body" style="top:18px;height:166px">
    <div class="head" style="height:36px;background:var(--blue-sky)">Packages</div>
    <svg style="margin:8px 0 4px" width="22" height="22"><rect x="2" y="8" width="18" height="13" fill="none" stroke="var(--red)" stroke-width="1.5"/><rect x="1" y="5" width="20" height="4" fill="none" stroke="var(--red)" stroke-width="1.5"/><path d="M11 5v16M11 5C8 0 5 2 7 5M11 5c3-5 6-3 4 0" stroke="var(--red)" fill="none" stroke-width="1.5"/></svg>
    <p>bluewake.example offers the best cruise deals and discounts on all cruise lines and cruise vacation packages worldwide. <a>Learn More &gt;</a></p>
    <div style="margin-top:9px"><span class="plan">CHOOSE PLAN</span></div>
  </div>
</div>
<div class="abs deal" style="left:214px">
  <div class="head" style="position:absolute;left:0;right:0;top:18px;height:47px;background:var(--blue-head);font-size:16px">Recommended</div>
  <svg style="position:absolute;left:80px;top:78px" width="24" height="26"><path d="M3 12h5v12H3zM8 13l5-10c3 0 3 3 2 7h6c2 0 2 3 0 3 2 1 1 3-1 3 1 1 0 3-2 3 1 1 0 3-2 3H8" fill="none" stroke="var(--red)" stroke-width="1.5"/></svg>
  <p style="position:absolute;top:114px;left:0;right:0">Let us put your mind at ease by answering questions about tickets, tipping, documentation, dress codes and more. <a>Learn More &gt;</a></p>
  <span class="plan abs" style="left:51px;top:167px">CHOOSE PLAN</span>
</div>
<div class="abs deal" style="left:399px">
  <div class="head" style="position:absolute;left:0;right:0;top:18px;height:47px;background:var(--blue-head);font-size:16px">Last Minute Deals</div>
  <svg style="position:absolute;left:79px;top:73px" width="24" height="30"><circle cx="12" cy="18" r="9" fill="none" stroke="var(--red)" stroke-width="1.5"/><path d="M9 3h6M12 3v6M12 18l3-4" stroke="var(--red)" stroke-width="1.5"/></svg>
  <p style="position:absolute;top:114px;left:0;right:0">Last minute cruises offer a great opportunity to get exceptional cruise deals, discounts, upgrades and other valuable offers on <a>Learn More &gt;</a></p>
  <span class="plan abs" style="left:51px;top:167px">CHOOSE PLAN</span>
</div>
<div class="abs deal" style="left:584px">
  <div class="body" style="top:18px;height:166px">
    <div class="head" style="height:36px;background:var(--blue-sky)">Harbor Star Cruise Deals</div>
    <div class="mini"><div class="thumb" role="img" aria-label="Ship deck view" style="background:linear-gradient(#9cc6e6,#c89a6a)"></div><span>4-Day Sales Event Featuring Exclusive Savings plus 3rd/4th Guest FREE</span></div>
    <div class="mini"><div class="thumb" role="img" aria-label="Couple on a cruise vacation" style="background:linear-gradient(#7fb6e0,#e8d4b8)"></div><span>FREE complimentary specialty dinner for 2 plus $50 onboard credit</span></div>
    <div style="margin-top:7px"><span class="plan">CHOOSE PLAN</span></div>
  </div>
</div>

<div class="abs partners">
  <h2>Our Partners</h2>
  <svg style="position:absolute;left:264px;top:22px" width="8" height="12"><path d="M7 1 2 6l5 5" stroke="#fff" stroke-width="2" fill="none"/></svg>
  <div class="plist"><span>NORTHWIND LINE</span><span>Corallo</span><span>REGENT ISLE</span><span>Starlit Voyages</span><span>MARISOL</span></div>
  <svg style="position:absolute;left:764px;top:22px" width="8" height="12"><path d="M1 1l5 5-5 5" stroke="#fff" stroke-width="2" fill="none"/></svg>
</div>

<div class="abs footer">
  <ul class="flist" style="left:98px"><li>Visa</li><li>About us</li><li>Contact us</li><li>Payment info</li></ul>
  <ul class="flist" style="left:260px"><li>Terms of privacy</li><li>Terms of service</li><li>Terms of insurance</li><li>Cooperation network</li></ul>
  <ul class="flist" style="left:444px"><li>Registration agreement</li><li>Cruise promotion policy</li><li>Booking process explanation</li><li>Bonus points collection policy</li></ul>
  <span class="social" style="left:643px;top:16px;background:#f5a623"></span>
  <span class="social" style="left:681px;top:16px;background:#2f6fb8"></span>
  <span class="social" style="left:643px;top:40px;background:#e8453c"></span>
  <span class="social" style="left:681px;top:40px;background:#6cc04a"></span>
  <span class="social" style="left:643px;top:64px;background:#3c8fd8"></span>
  <span class="social" style="left:681px;top:64px;background:#ef6a2a"></span>
  <div class="frule"></div>
  <div class="copy">Copyright © 2011 Bluewake Cruises All rights reserved<br>ICP No. 10000000</div>
</div>

</body>
</html>
```